TalkHarbor - Language Coaching Services

Sleek, innovative, trendy design for Language Coaching business.

TalkHarbor is a new UK based company that provides Language Coaching services. We offer highly personalized on-line and face to face language courses. We also impart learning techniques workshops based on the latest neuroscience research for second-language acquisition.

Target Market(s)

See attached info

Industry/Entity Type

Consulting

Contact Information for Business Card

TalkHarbor
DaniaKV@talkharbor.co.uk
TalkHarbor.co.uk
London, UK

Font styles to use
Sans Serif

```html
<!DOCTYPE html>
<html lang="en">
<head>
<meta charset="utf-8">
<title>TalkHarbor Business Card</title>
<link href="https://fonts.googleapis.com/css2?family=Oswald:wght@500&family=PT+Sans:wght@400;700&display=swap" rel="stylesheet">
<style>
  :root {
    --backdrop: #4a4a4c;
    --card: #232324;
    --brand-blue: #1f8fc2;
    --name-blue: #5a8fe2;
    --text-light: #ececec;
    --icon-blue: #6a92d8;
  }
  * { box-sizing: border-box; margin: 0; padding: 0; }
  html, body { width: 1200px; height: 1200px; overflow: hidden; }
  body {
    background: var(--backdrop);
    font-family: "PT Sans", sans-serif;
    display: flex;
    flex-direction: column;
    align-items: center;
    justify-content: center;
    gap: 40px;
  }
  .card {
    width: 960px;
    height: 549px;
    background: var(--card);
    position: relative;
    box-shadow: 0 12px 30px rgba(0,0,0,0.35);
  }
  .card-back {
    display: flex;
    align-items: center;
    justify-content: center;
  }
  .brand {
    display: flex;
    align-items: center;
    gap: 18px;
    color: var(--brand-blue);
    font-family: "PT Sans", sans-serif;
    font-weight: 400;
  }
  .brand-dot {
    border-radius: 50%;
    border: 6px solid var(--brand-blue);
  }
  .card-back .brand { font-size: 64px; }
  .card-back .brand-dot { width: 60px; height: 60px; }
  .card-front .brand {
    position: absolute;
    left: 70px;
    top: 50%;
    transform: translateY(-50%);
    font-size: 72px;
    letter-spacing: 1px;
  }
  .card-front .brand-dot { width: 64px; height: 64px; }
  .divider {
    position: absolute;
    left: 565px;
    top: 150px;
    width: 2px;
    height: 250px;
    background: linear-gradient(to bottom, transparent, var(--name-blue), transparent);
  }
  .contact {
    position: absolute;
    left: 615px;
    top: 140px;
    color: var(--text-light);
    font-size: 21px;
    line-height: 1.3;
  }
  .contact-name {
    font-family: "Oswald", sans-serif;
    font-weight: 500;
    color: var(--name-blue);
    font-size: 38px;
    line-height: 1.1;
  }
  .contact-role { margin-bottom: 18px; }
  .contact-address { margin-bottom: 14px; }
  .contact-list { list-style: none; }
  .contact-list li {
    display: flex;
    align-items: center;
    gap: 16px;
    margin-bottom: 4px;
  }
  .contact-list svg { width: 18px; height: 18px; flex: none; }
</style>
</head>
<body>
  <section class="card card-back">
    <div class="brand"><span class="brand-dot"></span>TalkHarbor</div>
  </section>

  <section class="card card-front">
    <div class="brand"><span class="brand-dot"></span>TalkHarbor</div>
    <div class="divider"></div>
    <div class="contact">
      <p class="contact-name">ELSA MARLOW</p>
      <p class="contact-role">President &amp; CEO</p>
      <p class="contact-address">Harbor Point Ltd, 14 Quay Lane,<br>Suite 2 London</p>
      <ul class="contact-list">
        <li>
          <svg viewBox="0 0 24 24" aria-hidden="true"><path fill="var(--icon-blue)" d="M6.6 10.8a15 15 0 0 0 6.6 6.6l2.2-2.2a1 1 0 0 1 1-.25 11.4 11.4 0 0 0 3.6.57 1 1 0 0 1 1 1V20a1 1 0 0 1-1 1A17 17 0 0 1 3 4a1 1 0 0 1 1-1h3.5a1 1 0 0 1 1 1c0 1.25.2 2.45.57 3.57a1 1 0 0 1-.25 1z"/></svg>
          +(000) -000- 0000
        </li>
        <li>
          <svg viewBox="0 0 24 24" aria-hidden="true"><rect x="2" y="5" width="20" height="14" fill="none" stroke="var(--icon-blue)" stroke-width="2"/><path d="M2 5l10 8 10-8" fill="none" stroke="var(--icon-blue)" stroke-width="2"/></svg>
          info@talkharbor.co.uk
        </li>
        <li>
          <svg viewBox="0 0 24 24" aria-hidden="true"><circle cx="12" cy="12" r="9" fill="none" stroke="var(--icon-blue)" stroke-width="2"/><path d="M3 12h18M12 3c3 3 3 15 0 18M12 3c-3 3-3 15 0 18" fill="none" stroke="var(--icon-blue)" stroke-width="1.5"/></svg>
          www.talkharbor.co.uk
        </li>
      </ul>
    </div>
  </section>
</body>
</html>
```